Modern Business Card

Modern professional business card with more than just logo and demographic info. Something memorable.

We are a trendy/modern chiropractic group with an emphasis on neurology, hence the minimalist-type brain logo. We want to convey that modern and technical aspect with professionalism and the elite nature of our practice environment.

```html
<!DOCTYPE html>
<html lang="en">
<head>
<meta charset="utf-8">
<title>Meridian Spine Studio – Business Card</title>
<link href="https://fonts.googleapis.com/css2?family=Cinzel:wght@500&family=Lato:wght@400&family=Fira+Sans:wght@400;600&display=swap" rel="stylesheet">
<style>
  :root {
    --backdrop: #3a3a3a;
    --card-black: #1d1d1f;
    --card-front: #19191a;
    --brand-blue: #4a6cad;
    --swoosh-grey: #3b3b3e;
    --white: #ffffff;
    --front-mark: #5c5c60;
  }
  html, body {
    margin: 0;
    padding: 0;
    width: 799px;
    height: 1200px;
    overflow: hidden;
    background: var(--backdrop);
  }
  .canvas {
    width: 799px;
    height: 1200px;
    display: flex;
    flex-direction: column;
    align-items: center;
    justify-content: space-around;
  }
  .card {
    position: relative;
    width: 580px;
    height: 332px;
    border-radius: 4px;
    overflow: hidden;
    box-shadow: 0 14px 30px rgba(0,0,0,0.45);
  }
  /* Front */
  .card-front {
    background: var(--card-front);
    display: flex;
    align-items: center;
    justify-content: center;
    gap: 16px;
  }
  .front-square {
    width: 26px;
    height: 26px;
    background: var(--front-mark);
  }
  .front-name {
    font-family: "Cinzel", serif;
    font-weight: 500;
    font-size: 34px;
    letter-spacing: 2px;
    color: var(--front-mark);
  }
  /* Back */
  .card-back { background: var(--card-black); }
  .brand {
    position: absolute;
    left: 34px;
    top: 24px;
    display: flex;
    align-items: center;
    gap: 14px;
  }
  .brand-square {
    width: 40px;
    height: 40px;
    background: var(--brand-blue);
  }
  .brand-name {
    font-family: "Cinzel", serif;
    font-weight: 500;
    font-size: 28px;
    line-height: 29px;
    color: var(--white);
    letter-spacing: 1px;
  }
  .contact {
    position: absolute;
    left: 34px;
    top: 96px;
    margin: 0;
    padding: 0;
    list-style: none;
    font-family: "Lato", sans-serif;
    font-size: 13.5px;
    color: var(--white);
  }
  .contact li {
    display: flex;
    align-items: center;
    gap: 8px;
    height: 20px;
  }
  .contact .address { padding-left: 20px; }
  .contact svg { width: 12px; height: 12px; fill: var(--brand-blue); flex: none; }
  .waves {
    position: absolute;
    left: 0;
    top: 0;
    width: 580px;
    height: 332px;
  }
  .person {
    position: absolute;
    right: 36px;
    bottom: 12px;
    text-align: left;
    color: var(--white);
    font-family: "Fira Sans", sans-serif;
  }
  .person-name { font-weight: 600; font-size: 22px; line-height: 26px; }
  .person-title { font-weight: 400; font-size: 15px; line-height: 18px; }
</style>
</head>
<body>
<main class="canvas">
  <section class="card card-front" aria-label="Card front">
    <span class="front-square"></span>
    <span class="front-name">Meridian Spine Studio</span>
  </section>

  <section class="card card-back" aria-label="Card back">
    <svg class="waves" viewBox="0 0 580 332" aria-hidden="true">
      <path d="M0 195 C 70 245, 150 282, 250 284 C 370 286, 470 240, 580 180 L580 332 L0 332 Z" fill="var(--swoosh-grey)"/>
      <path d="M0 180 C 70 230, 150 268, 250 270 C 370 272, 470 225, 580 165 L580 185 C 470 245, 370 290, 250 290 C 150 290, 70 252, 0 200 Z" fill="var(--white)"/>
      <path d="M0 222 C 70 268, 150 302, 250 304 C 370 306, 470 262, 580 205 L580 332 L0 332 Z" fill="var(--brand-blue)"/>
    </svg>

    <div class="brand">
      <span class="brand-square"></span>
      <span class="brand-name">Meridian<br>Spine Studio</span>
    </div>

    <ul class="contact">
      <li class="address">87 Larkfield Ave., Brookvale, US 40213</li>
      <li><svg viewBox="0 0 12 12"><path d="M2 1h3l1 3-1.5 1a6 6 0 0 0 2.5 2.5L8 6l3 1v3a1 1 0 0 1-1 1A9 9 0 0 1 1 2a1 1 0 0 1 1-1z"/></svg>555-014-2277</li>
      <li><svg viewBox="0 0 12 12"><path d="M0 2h12v8H0z"/></svg>alex@meridianspine.com</li>
      <li><svg viewBox="0 0 12 12"><circle cx="6" cy="6" r="6"/></svg>www.meridianspine.com</li>
    </ul>

    <div class="person">
      <div class="person-name">Alex Rowan Hale</div>
      <div class="person-title">Managing Director</div>
    </div>
  </section>
</main>
</body>
</html>
```